Event flyer for Sunday night Youth Group

Need a 4 x 6 or 5 x 7 flyer for a new youth group starting on April 14. The youth group is for students in middle school and high school so it needs to look fun and cool, but not childish. I prefer it not to include pictures of people unless it's so obscure you can't really see their faces. I've uploaded some pictures of flyers I like. I've also attached a couple versions of our logo to use on the flyer.
Information the flyer needs to include:
Youth Group
Sundays, 6-8pm (beginning April 14)
Location: Marlowe's - 4219 Quarry Fern Ave N, Keizer, 97318
There will be dinner, games, friends, and a message.
Target Market(s)
Youth ages 13-18
Industry/Entity Type
Church
Font styles to use
Colors
Designer to choose colors to be used in the design.
Look and feel

```html
<!DOCTYPE html>
<html lang="en">
<head>
<meta charset="utf-8">
<title>Youth Groups – Sunday Nights</title>
<link rel="stylesheet" href="https://fonts.googleapis.com/css2?family=Archivo:wdth,wght@62..125,100..900&family=Roboto+Condensed:wght@300;700&family=Rubik:wght@800&display=swap">
<style>
  :root {
    --sky-top: #d6e7f8;
    --sky-bottom: #a7c7ec;
    --yellow: #f7c53f;
    --yellow-deep: #e9a823;
    --blue: #2f74d6;
    --blue-light: #4a8ee6;
    --lime: #c8e02c;
    --lime-light: #d9ec4a;
    --red: #e52527;
    --red-deep: #a80c10;
    --paper: #f4f4f2;
    --ink: #ffffff;
    --brand: #264a57;
  }
  * { margin: 0; padding: 0; box-sizing: border-box; }
  html, body { width: 1000px; height: 1200px; overflow: hidden; }
  .flyer {
    position: relative;
    width: 1000px;
    height: 1200px;
    background: linear-gradient(160deg, var(--sky-top) 0%, var(--sky-bottom) 100%);
  }
  .artwork { position: absolute; inset: 0; }
  .location-label { font-family: "Roboto Condensed", sans-serif; font-weight: 300; }
  .location-line { font-family: "Roboto Condensed", sans-serif; font-weight: 700; }
  .schedule-line { font-family: "Rubik", sans-serif; font-weight: 800; }
  .headline { font-family: "Archivo", sans-serif; font-weight: 900; font-stretch: 125%; font-variation-settings: "wdth" 125; }
  .tagline { font-family: "Archivo", sans-serif; font-weight: 800; font-stretch: 125%; font-variation-settings: "wdth" 125; }
  .brand {
    position: absolute;
    left: 44px;
    bottom: 54px;
    display: flex;
    align-items: center;
    gap: 12px;
  }
  .brand-mark { width: 22px; height: 22px; background: var(--brand); }
  .brand-name {
    font-family: "Archivo", sans-serif;
    font-weight: 800;
    font-size: 24px;
    letter-spacing: 0.04em;
    color: var(--brand);
  }
</style>
</head>
<body>
<main class="flyer">
  <svg class="artwork" viewBox="0 0 1000 1200" width="1000" height="1200">
    <defs>
      <linearGradient id="yellowSheen" x1="0" y1="0" x2="1" y2="1">
        <stop offset="0" stop-color="#fcd45a"/>
        <stop offset="1" stop-color="#e9a823"/>
      </linearGradient>
      <linearGradient id="blueSheen" x1="0" y1="0" x2="1" y2="1">
        <stop offset="0" stop-color="#4a8ee6"/>
        <stop offset="1" stop-color="#2f74d6"/>
      </linearGradient>
      <radialGradient id="limeSheen" cx="0.45" cy="0.7" r="0.7">
        <stop offset="0" stop-color="#d9ec4a"/>
        <stop offset="1" stop-color="#c8e02c"/>
      </radialGradient>
      <linearGradient id="redSheen" x1="0" y1="0" x2="1" y2="0">
        <stop offset="0" stop-color="#e52527"/>
        <stop offset="0.85" stop-color="#e52527"/>
        <stop offset="1" stop-color="#a80c10"/>
      </linearGradient>
      <filter id="softShadow" x="-20%" y="-20%" width="140%" height="140%">
        <feDropShadow dx="0" dy="6" stdDeviation="8" flood-color="#1b3c6b" flood-opacity="0.18"/>
      </filter>
    </defs>

    <g class="location-sticker" filter="url(#softShadow)">
      <polygon fill="url(#yellowSheen)"
        points="0,220 212,98 268,108 455,350 275,455 262,450 240,462 222,458 200,470 180,466 160,478 140,474 118,486 100,500 88,520 80,526 0,472"/>
      <polygon fill="var(--paper)" points="254,96 268,108 283,112 278,96"/>
      <polygon fill="url(#yellowSheen)"
        points="122,585 140,574 160,570 182,556 200,554 222,540 240,530 255,525 300,600 180,682"/>
      <g transform="translate(228,318) rotate(-30)" fill="var(--ink)" text-anchor="middle">
        <text class="location-label" x="-20" y="-52" font-size="31">Location:</text>
        <text class="location-line" x="0" y="-12" font-size="35">Marlowe's - 4219</text>
        <text class="location-line" x="0" y="28" font-size="35">Quarry Fern Ave N,</text>
        <text class="location-line" x="0" y="68" font-size="35">Keizer, 97318</text>
      </g>
    </g>

    <g class="schedule-sticker" filter="url(#softShadow)">
      <polygon fill="url(#blueSheen)" points="606,371 875,252 888,262 870,657 855,652"/>
      <g transform="translate(805,400) rotate(39)" fill="var(--ink)" text-anchor="middle">
        <text class="schedule-line" x="30" y="-40" font-size="26">Sundays</text>
        <text class="schedule-line" x="15" y="-8" font-size="26">6-8pm</text>
        <text class="schedule-line" x="0" y="24" font-size="26">(beginning</text>
        <text class="schedule-line" x="-10" y="56" font-size="26">April 14)</text>
      </g>
    </g>

    <g class="details-banner" filter="url(#softShadow)">
      <polygon fill="url(#redSheen)"
        points="278,889 880,746 1000,860 1000,914 554,1008 530,1012 508,1020 480,1016 456,1024 430,1022 400,1028 372,1030 348,1040 330,1046 314,1050"/>
      <polygon fill="var(--paper)" points="880,746 905,748 975,830 1000,860"/>
      <g transform="translate(352,962) rotate(-13.5)" fill="var(--ink)">
        <text class="tagline" x="0" y="0" font-size="34" textLength="575" lengthAdjust="spacingAndGlyphs">THERE WILL BE DINNER, GAMES,</text>
        <text class="tagline" x="8" y="46" font-size="34" textLength="470" lengthAdjust="spacingAndGlyphs">FRIENDS, AND A MESSAGE.</text>
      </g>
    </g>

    <g class="title-disc" filter="url(#softShadow)">
      <circle cx="490" cy="614" r="268" fill="url(#limeSheen)"/>
      <g transform="rotate(-4 490 680)" fill="var(--ink)" text-anchor="middle">
        <text class="headline" x="492" y="644" font-size="98">YOUTH</text>
        <text class="headline" x="498" y="722" font-size="98">GROUPS</text>
      </g>
    </g>
  </svg>

  <div class="brand">
    <span class="brand-mark"></span>
    <span class="brand-name">WAYFIELD FELLOWSHIP</span>
  </div>
</main>
</body>
</html>
```